creative brochure for lumawell advisory an innovative consulting company!

Im looking for a brochure to be designed. I am happy for the designer to be creative with it. Please use the colors from my logo and you can look at my website www.lumawelladvisory.example to get a feel. I will provide all the wording. Its aimed at small business owners and i want it to give off the vibe of professional and experienced.
The text logo and a photo of me is attached. Please edit the photo of me to make me look slimmer!
If you want to change text because you can make it sound better please go ahead. use my website to see if there is any other information in it that would make the brochure better or more credible/convincing.
I am open to ideas, lay out and how many pages it should be or if it should be double sided. I need one i can email and one i can print. Maybe use the sentence "Turn your business around now as the point which jumps out the most".
Updates

I have just uploaded a bigger version of the photo as requested. Please photoshop it to make me look thinner and perhaps crop it at the waist. Thanks

Hi everyone, great work so far. Im liking the designs. Maybe just a bit less color. you could use grey i guess or other plain colors. Im not a fan of the orange in my logo so just use it minimally in the next ones. Still considering the ones submitted though.

Hi everyone, please remove the words, jumps out as the main point and just have, turn your business around now.

Thanks

Could you please also include this email address in the contact details

maren.toovey@lumawelladvisory.example

Please change the words Turn your business around too unlock your business potential now.

Target Market(s)

Small business in australia

Industry/Entity Type

Small Business

Requirements
Must have
• as above, all that i have provided in the files must be used as a minimum
Nice to have
• great creative use of my brand colors
Should not have
• i dont want it to look to young or too over the top. I dont want any new colors.

```html
<!DOCTYPE html>
<html lang="en">
<head>
<meta charset="utf-8">
<title>Lumawell Advisory – Brochure Spread</title>
<link rel="stylesheet" href="https://fonts.googleapis.com/css2?family=PT+Sans:ital,wght@0,400;0,700;1,700&family=Ubuntu:wght@400;500;700&display=swap">
<style>
  :root {
    --backdrop: #3b3b3b;
    --paper: #ffffff;
    --paper-soft: #f1f2f3;
    --paper-grey: #dfe1e3;
    --band-grey: #e8eaec;
    --ink: #4f4f4f;
    --ink-soft: #6e6e6e;
    --ink-strong: #3a3a3a;
    --brand-blue: #2c7cc0;
    --ribbon-dark: #1f6cab;
    --ribbon-light: #78b8e4;
    --tab-grey: #c7c9cb;
    --tab-ink: #505050;
  }
  * { box-sizing: border-box; margin: 0; padding: 0; }
  html, body { width: 1200px; height: 899px; overflow: hidden; }
  body { background: var(--backdrop); font-family: "PT Sans", Arial, sans-serif; color: var(--ink); position: relative; }

  .spread { position: absolute; left: 50px; top: 70px; width: 1100px; height: 760px; display: flex; box-shadow: 0 18px 40px rgba(0,0,0,.45); }
  .page { position: relative; width: 550px; height: 760px; background: var(--paper); overflow: hidden; }
  .page--left { box-shadow: inset -18px 0 24px -18px rgba(0,0,0,.25); }
  .page--right { box-shadow: inset 18px 0 24px -18px rgba(0,0,0,.25); }

  .band { position: absolute; left: 0; width: 100%; }
  .band svg { display: block; }
  .band--top { top: 0; height: 330px; background: linear-gradient(180deg, var(--paper-grey), var(--paper-soft)); }
  .band--middle { top: 300px; height: 290px; background: linear-gradient(180deg, var(--band-grey), var(--paper-soft)); }
  .curve { position: absolute; left: 0; width: 100%; }

  /* numbered ribbons */
  .ribbons { position: absolute; left: 18px; top: 70px; }
  .ribbon { position: relative; width: 470px; height: 48px; margin-bottom: 24px; }
  .ribbon svg { position: absolute; inset: 0; }
  .ribbon__num { position: absolute; left: 12px; top: 11px; font-family: "Ubuntu", sans-serif; font-weight: 500; font-size: 22px; color: var(--tab-ink); }
  .ribbon__text { position: absolute; left: 96px; top: 14px; font-family: "PT Sans", sans-serif; font-weight: 700; font-size: 15px; color: #fff; letter-spacing: .2px; text-shadow: 0 1px 1px rgba(0,0,0,.25); }
  .ribbon:nth-child(2) .ribbon__text { font-size: 14px; left: 88px; }

  .tailor-heading { position: absolute; left: 30px; top: 332px; font-family: "Ubuntu", sans-serif; font-weight: 500; font-size: 17px; color: var(--brand-blue); text-transform: uppercase; letter-spacing: .2px; }

  .checklist { list-style: none; position: absolute; }
  .checklist li { display: flex; align-items: flex-start; gap: 10px; font-size: 16px; line-height: 1.3; color: var(--ink); }
  .checklist svg { flex: none; margin-top: 2px; }
  .checklist--services { left: 250px; top: 370px; }
  .checklist--services li { margin-bottom: 9px; }
  .checklist--values { left: 40px; top: 270px; width: 470px; }
  .checklist--values li { margin-bottom: 12px; }
  .keyword { color: var(--brand-blue); font-weight: 700; text-transform: uppercase; }

  .photo { position: absolute; left: 0; top: 440px; width: 240px; height: 150px; background: linear-gradient(135deg, #c9ccd0, #9a9ea3 60%, #6f7276); }

  .slogan { position: absolute; font-family: "PT Sans", sans-serif; font-weight: 700; font-size: 23px; color: var(--ink-soft); text-transform: uppercase; letter-spacing: 1px; line-height: 1.45; }
  .slogan--left { left: 60px; top: 650px; }
  .slogan--left .indent { display: block; padding-left: 150px; }
  .slogan--right { left: 50px; top: 620px; }

  .intro { position: absolute; left: 40px; top: 36px; width: 470px; font-size: 16px; line-height: 1.55; color: var(--ink-soft); }
  .values-heading { position: absolute; left: 40px; top: 160px; width: 480px; font-family: "Ubuntu", sans-serif; font-weight: 500; font-size: 21px; line-height: 1.35; color: var(--ink-strong); }
  .band--values { top: 230px; height: 330px; background: linear-gradient(180deg, var(--band-grey), var(--paper-soft)); }
</style>
</head>
<body>
<main class="spread">

  <section class="page page--left">
    <div class="band band--top"></div>
    <div class="band band--middle"></div>
    <svg class="curve" style="top:290px" width="550" height="50" viewBox="0 0 550 50" aria-hidden="true">
      <path d="M0 40 C150 0 350 0 550 20 L550 50 L0 50 Z" fill="#e8eaec"/>
      <path d="M0 40 C150 0 350 0 550 20" fill="none" stroke="#ffffff" stroke-width="3"/>
    </svg>

    <div class="ribbons">
      <div class="ribbon">
        <svg width="470" height="48" viewBox="0 0 470 48" aria-hidden="true">
          <defs><linearGradient id="rib1" x1="0" x2="1"><stop offset="0" stop-color="#1f6cab"/><stop offset="1" stop-color="#78b8e4"/></linearGradient></defs>
          <polygon points="56,6 470,6 452,24 470,42 56,42" fill="url(#rib1)"/>
          <polygon points="0,0 58,0 76,24 58,48 0,48" fill="#c7c9cb"/>
        </svg>
        <span class="ribbon__num">01</span>
        <span class="ribbon__text">Lumawell Advisory presents Clear Horizon Strategy.</span>
      </div>
      <div class="ribbon">
        <svg width="470" height="48" viewBox="0 0 470 48" aria-hidden="true">
          <polygon points="56,6 470,6 452,24 470,42 56,42" fill="url(#rib1)"/>
          <polygon points="0,0 58,0 76,24 58,48 0,48" fill="#c7c9cb"/>
        </svg>
        <span class="ribbon__num">02</span>
        <span class="ribbon__text">Affordable one on one Corporate services for small business.</span>
      </div>
      <div class="ribbon">
        <svg width="470" height="48" viewBox="0 0 470 48" aria-hidden="true">
          <polygon points="56,6 470,6 452,24 470,42 56,42" fill="url(#rib1)"/>
          <polygon points="0,0 58,0 76,24 58,48 0,48" fill="#c7c9cb"/>
        </svg>
        <span class="ribbon__num">03</span>
        <span class="ribbon__text">Lumawell Advisory presents Clear Horizon Strategy.</span>
      </div>
    </div>

    <h2 class="tailor-heading">Lumawell will tailor solutions to transform your business</h2>

    <ul class="checklist checklist--services">
      <li><svg width="16" height="16" viewBox="0 0 16 16" aria-hidden="true"><path d="M2 9 L6 13 L14 2" fill="none" stroke="#222" stroke-width="2.4"/></svg>Sales Strategies.</li>
      <li><svg width="16" height="16" viewBox="0 0 16 16" aria-hidden="true"><path d="M2 9 L6 13 L14 2" fill="none" stroke="#222" stroke-width="2.4"/></svg>Marketing expertise.</li>
      <li><svg width="16" height="16" viewBox="0 0 16 16" aria-hidden="true"><path d="M2 9 L6 13 L14 2" fill="none" stroke="#222" stroke-width="2.4"/></svg>Growth Strategies.</li>
      <li><svg width="16" height="16" viewBox="0 0 16 16" aria-hidden="true"><path d="M2 9 L6 13 L14 2" fill="none" stroke="#222" stroke-width="2.4"/></svg>Business coaching.</li>
      <li><svg width="16" height="16" viewBox="0 0 16 16" aria-hidden="true"><path d="M2 9 L6 13 L14 2" fill="none" stroke="#222" stroke-width="2.4"/></svg>Customer Service training</li>
    </ul>

    <div class="photo" role="img" aria-label="Photo of a business owner working at a laptop"></div>

    <svg class="curve" style="top:560px" width="550" height="70" viewBox="0 0 550 70" aria-hidden="true">
      <path d="M0 30 C180 70 380 60 550 0 L550 70 L0 70 Z" fill="#ffffff"/>
      <path d="M0 30 C180 70 380 60 550 0" fill="none" stroke="#d3d6d9" stroke-width="2"/>
    </svg>

    <p class="slogan slogan--left">We work with potential,<span class="indent">not just problems.</span></p>
  </section>

  <section class="page page--right">
    <p class="intro">Traditional consulting firms work with the problems within a business or project. All Lumawell Advisory solutions are designed to work with the <span class="keyword">potential</span> of your business. This means we don't just make things better, we realise what's possible.</p>

    <h2 class="values-heading">Our Values are reflected in the choices we make for ourselves and our clients, every day.</h2>

    <div class="band band--values"></div>
    <svg class="curve" style="top:222px" width="550" height="40" viewBox="0 0 550 40" aria-hidden="true">
      <path d="M0 10 C200 40 380 30 550 0 L550 40 L0 40 Z" fill="#e8eaec"/>
      <path d="M0 10 C200 40 380 30 550 0" fill="none" stroke="#ffffff" stroke-width="3"/>
    </svg>

    <ul class="checklist checklist--values">
      <li><svg width="16" height="16" viewBox="0 0 16 16" aria-hidden="true"><path d="M2 9 L6 13 L14 2" fill="none" stroke="#222" stroke-width="2.4"/></svg><span>We choose <span class="keyword">courage</span> over fear.</span></li>
      <li><svg width="16" height="16" viewBox="0 0 16 16" aria-hidden="true"><path d="M2 9 L6 13 L14 2" fill="none" stroke="#222" stroke-width="2.4"/></svg><span>We <span class="keyword">collaborate</span> to create unique solutions together.</span></li>
      <li><svg width="16" height="16" viewBox="0 0 16 16" aria-hidden="true"><path d="M2 9 L6 13 L14 2" fill="none" stroke="#222" stroke-width="2.4"/></svg><span>We <span class="keyword">commit</span> by doing what we say we'll do.</span></li>
      <li><svg width="16" height="16" viewBox="0 0 16 16" aria-hidden="true"><path d="M2 9 L6 13 L14 2" fill="none" stroke="#222" stroke-width="2.4"/></svg><span>We are <span class="keyword">creative</span> because we always look for and explore fresh ideas.</span></li>
      <li><svg width="16" height="16" viewBox="0 0 16 16" aria-hidden="true"><path d="M2 9 L6 13 L14 2" fill="none" stroke="#222" stroke-width="2.4"/></svg><span>We have <span class="keyword">fun</span>, because we bring humor and lightness to each day.</span></li>
    </ul>

    <svg class="curve" style="top:500px" width="550" height="80" viewBox="0 0 550 80" aria-hidden="true">
      <path d="M0 0 C160 50 400 60 550 30 L550 80 L0 80 Z" fill="#ffffff"/>
      <path d="M0 0 C160 50 400 60 550 30" fill="none" stroke="#d3d6d9" stroke-width="2"/>
    </svg>

    <p class="slogan slogan--right">We value courage, commitment,<br>collaboration, creativity, and fun.</p>
  </section>

</main>
</body>
</html>
```